New business card/stationary for a consulting company

I am looking for a clean and very professional looking business card for my consulting company as well as corresponding stationary. I am uploading our logo. I like simple and powerful for the feel. No graphics but I am open on everything else. Below is my contact information but would like the final to be in a version I can add my employees information into and print. Thank you.

Daniel Whitcombe
dan@ferncliffadvisory.com
2870 North 9th Avenue, Summit Floor, Elm Ridge, Illinois 60531
www.ferncliffadvisory.com

Industry/Entity Type

Consulting

Contact Information for Business Card

Daniel Whitcombe
dan@ferncliffadvisory.com
www.ferncliffadvisory.com

Font styles to use
Serif
Sans Serif

Requirements
Must have
• Our logo and the business card details.
Nice to have
• our website www.ferncliffadvisory.com

```html
<!DOCTYPE html>
<html lang="en">
<head>
<meta charset="utf-8">
<title>Ferncliff Advisory – Business Card</title>
<link rel="stylesheet" href="https://fonts.googleapis.com/css2?family=Open+Sans:wght@400;700&family=Questrial&display=swap">
<style>
  :root {
    --navy: #070b5f;
    --paper: #ffffff;
    --paper-shade: #f1f1f3;
    --ink-grey: #6e6e72;
    --backdrop: #e6e6e8;
  }
  * { box-sizing: border-box; margin: 0; padding: 0; }
  html, body { width: 1200px; height: 904px; overflow: hidden; }
  body {
    background: var(--backdrop);
    display: flex;
    flex-direction: column;
    align-items: center;
    justify-content: center;
    gap: 44px;
    font-family: "Open Sans", sans-serif;
  }
  .card {
    width: 690px;
    height: 394px;
    box-shadow: 0 6px 18px rgba(0,0,0,0.18);
    position: relative;
  }
  .card-back {
    background: var(--navy);
    display: flex;
    align-items: center;
    justify-content: center;
  }
  .back-wordmark {
    font-family: "Questrial", sans-serif;
    color: var(--paper);
    font-size: 30px;
    letter-spacing: 4px;
    text-transform: uppercase;
  }
  .card-front {
    background: linear-gradient(135deg, var(--paper-shade), var(--paper) 45%, var(--paper-shade));
    display: flex;
    flex-direction: column;
    align-items: center;
    padding-top: 78px;
  }
  .brand {
    display: flex;
    align-items: center;
    gap: 14px;
  }
  .brand-square {
    width: 26px;
    height: 26px;
    background: var(--navy);
  }
  .brand-name {
    font-family: "Questrial", sans-serif;
    color: var(--navy);
    font-size: 27px;
    letter-spacing: 2px;
    text-transform: uppercase;
  }
  .contact {
    margin-top: 96px;
    text-align: center;
  }
  .person-name {
    color: var(--navy);
    font-weight: 700;
    font-size: 19px;
    margin-bottom: 6px;
  }
  .contact-line {
    color: var(--ink-grey);
    font-size: 13.5px;
    line-height: 1.55;
    display: flex;
    align-items: center;
    justify-content: center;
    gap: 6px;
  }
  .contact-line svg { width: 14px; height: 14px; }
  .divider { margin: 0 4px; }
</style>
</head>
<body>
  <section class="card card-back">
    <span class="back-wordmark">Ferncliff Advisory</span>
  </section>

  <section class="card card-front">
    <div class="brand">
      <span class="brand-square"></span>
      <span class="brand-name">Ferncliff Advisory</span>
    </div>
    <div class="contact">
      <p class="person-name">Daniel Whitcombe</p>
      <p class="contact-line">2870 North 9th Avenue, Summit Floor, Elm Ridge, Illinois 60531</p>
      <p class="contact-line">
        <svg viewBox="0 0 16 16" aria-hidden="true"><circle cx="8" cy="8" r="8" fill="#070b5f"/><rect x="4" y="5.5" width="8" height="5.5" fill="none" stroke="#fff" stroke-width="1"/><polyline points="4,5.5 8,8.6 12,5.5" fill="none" stroke="#fff" stroke-width="1"/></svg>
        dan@ferncliffadvisory.com
        <span class="divider">|</span>
        <svg viewBox="0 0 16 16" aria-hidden="true"><circle cx="8" cy="8" r="8" fill="#070b5f"/><circle cx="8" cy="8" r="4.5" fill="none" stroke="#fff" stroke-width="1"/><ellipse cx="8" cy="8" rx="2" ry="4.5" fill="none" stroke="#fff" stroke-width="1"/><line x1="3.5" y1="8" x2="12.5" y2="8" stroke="#fff" stroke-width="1"/></svg>
        www.ferncliffadvisory.com
      </p>
    </div>
  </section>
</body>
</html>
```